Firm-Asset: Tomorrow - EU-funded management consulting

A website to inform possible customers about my management consulting services for small and medium sized companies. I am using a funding for small and medium companies to do 10 days of workshops and coaching about leadership, further education and employee's health. The Funding is called "Betriebsgut Zukunft" which means something like: Humans are the value of the company. The official logo is attached as a

Target Market(s)

Small and medium sized companies that want to improve their employee's well being and efficiency.

Industry/Entity Type

Management Consulting

Contact Information for Business Card

Malte Quast, Birkenhainweg 14, 10219 Berlin

Logo Text

BetriebsGut Zukunft - Beratung

Font styles to use
Serif
Sans Serif

Requirements
Must have
• a friendly and professional design
Nice to have
• saying somthing about: employees, leadership, further education and employees health are important to us.
Should not have
• should not be too shimmering

```html
<!DOCTYPE html>
<html lang="en">
<head>
<meta charset="utf-8">
<title>Betriebsgut Zukunft – Beratung</title>
<link rel="stylesheet" href="https://fonts.googleapis.com/css2?family=Open+Sans:wght@400;600;700;800&display=swap">
<style>
:root{
  --navy:#0c1a24;
  --dark:#141c22;
  --blue:#1e7fb0;
  --blue-dark:#14628c;
  --orange:#c7822e;
  --text:#555b60;
  --light:#f4f5f6;
  --line:#e1e4e7;
  --white:#ffffff;
}
*{box-sizing:border-box;margin:0;padding:0}
html,body{width:1200px;height:2384px;overflow:hidden}
body{font-family:"Open Sans",Arial,sans-serif;color:var(--text);background:var(--white);position:relative}
a{color:inherit;text-decoration:none}

.topnav{height:40px;background:var(--navy);display:flex;align-items:center;padding-left:30px}
.topnav a{color:#cfd6db;font-size:12px;font-weight:700;letter-spacing:.5px;padding:0 20px;height:40px;line-height:40px}
.topnav a.active{background:var(--blue);color:var(--white)}
.topnav .search{margin-left:auto;margin-right:40px}

.header{height:160px;display:flex;align-items:center;justify-content:space-between;padding:0 100px}
.brand{display:flex;align-items:center;gap:12px}
.brand-mark{width:44px;height:44px;background:var(--blue)}
.brand-name{font-size:30px;font-weight:700;color:var(--blue-dark);line-height:1}
.brand-tag{margin-top:6px;background:var(--blue);color:var(--white);font-size:10px;font-weight:700;letter-spacing:1.5px;padding:3px 10px;display:inline-block}
.social{display:flex;gap:14px}
.social span{width:28px;height:28px;border-radius:50%;border:1px solid #b8bfc5;background:var(--light)}

.hero{height:580px;position:relative;background:linear-gradient(135deg,#3a4148 0%,#252b31 45%,#4b525a 100%);display:flex;flex-direction:column;align-items:center;justify-content:center}
.hero-photo{position:absolute;inset:0;background:radial-gradient(ellipse at 70% 40%,rgba(140,150,160,.35),transparent 60%)}
.hero h1{position:relative;color:var(--white);font-size:44px;font-weight:800;letter-spacing:2px;margin-top:20px}
.hero p{position:relative;color:#d9dee2;font-size:14px;letter-spacing:6px;font-weight:600;margin-top:6px}
.hero .arrow{position:absolute;top:280px}
.hero .prev{left:30px}.hero .next{right:30px}

.welcome{padding:40px 120px 0;text-align:center}
.welcome h2{font-size:30px;font-weight:400;color:#333}
.welcome h2 em{font-style:normal;color:var(--blue)}
.welcome p{font-size:13px;line-height:22px;margin:20px auto 0;width:940px}

.cards{display:flex;gap:40px;padding:0 100px;margin-top:60px}
.card{width:220px;border:1px solid var(--line);background:var(--white)}
.card-head{height:110px;display:flex;flex-direction:column;align-items:center;padding-top:12px}
.card-head.blue{background:var(--blue)}
.card-head.orange{background:var(--orange)}
.card-head h3{color:var(--white);font-size:10px;font-weight:700;letter-spacing:1px}
.card-icon{width:62px;height:62px;border-radius:50%;background:var(--white);margin-top:12px;display:flex;align-items:center;justify-content:center}
.card p{font-size:12px;line-height:19px;padding:16px 22px 0;text-align:center}
.card .more{display:flex;justify-content:space-between;margin:18px 14px 14px;padding-top:8px;border-top:1px solid var(--line);font-size:11px;font-weight:600;color:var(--blue)}

.services{position:absolute;top:1360px;left:0;width:1200px;height:440px;background:linear-gradient(180deg,#1b2228,#0f1418);text-align:center}
.services h2{color:var(--white);font-size:28px;font-weight:400;margin-top:40px}
.services .sub{color:#aab3ba;font-size:11px;margin-top:6px}
.service-row{display:flex;gap:20px;padding:0 100px;margin-top:30px}
.service{width:320px}
.service-photo{height:170px;background:linear-gradient(135deg,#c9ccd0,#8d959c)}
.service-foot{display:flex;justify-content:space-between;align-items:center;height:42px;color:var(--white);font-size:13px}
.service-foot .btn{background:var(--blue);color:var(--white);font-size:11px;padding:5px 16px}

.testimonials{position:absolute;top:1840px;left:0;width:1200px;text-align:center}
.testimonials h2{font-size:28px;font-weight:400;color:var(--blue)}
.testimonials .rule{width:260px;height:1px;background:var(--line);margin:12px auto 0}
.quote-wrap{display:flex;align-items:flex-start;gap:40px;width:900px;margin:36px auto 0;text-align:left}
.avatar{width:120px;height:120px;border-radius:50%;background:linear-gradient(135deg,#8b95a0,#3e4852);flex:none}
.quote{font-size:13px;line-height:22px;font-style:italic;position:relative;padding:0 40px}
.quote .mark{position:absolute;font-size:42px;color:#c8ccd0;font-style:normal}
.quote .open{left:0;top:-8px}.quote .close{right:0;bottom:-28px}
.quote .who{font-style:normal;color:var(--blue);margin-top:14px;font-size:12px}
.quote .role{font-style:normal;font-size:12px}

.footer{position:absolute;top:2150px;left:0;width:1200px;height:210px;background:var(--dark);display:flex;gap:40px;padding:26px 100px 0}
.footer h4{color:var(--white);font-size:12px;font-weight:700;margin-bottom:12px}
.footer li{list-style:none;color:#aab3ba;font-size:11px;line-height:21px}
.footer li::before{content:"›";color:var(--blue);margin-right:8px}
.col-about{width:150px}.col-service{width:190px}.col-contact{width:300px}
.form{display:grid;grid-template-columns:1fr 1fr;gap:8px}
.form span{background:#232c33;color:#8b959c;font-size:10px;padding:6px 8px}
.form .submit{grid-column:1;background:var(--blue);color:var(--white);width:60px;text-align:center}
.col-q p{color:#aab3ba;font-size:11px;line-height:22px}
.col-q p.loc{color:var(--blue)}
.bottombar{position:absolute;top:2360px;left:0;width:1200px;height:24px;background:#0a0f12;display:flex;justify-content:space-between;align-items:center;padding:0 20px;color:#7d878e;font-size:9px}
</style>
</head>
<body>

<nav class="topnav">
  <a class="active">HOME</a><a>ABOUT US</a><a>SERVICES</a><a>BLOG</a><a>TESTIMONIALS</a><a>CONTACTS</a>
  <a class="search"><svg width="14" height="14" viewBox="0 0 14 14"><circle cx="6" cy="6" r="4.5" fill="none" stroke="#cfd6db" stroke-width="1.6"/><line x1="9.3" y1="9.3" x2="13" y2="13" stroke="#cfd6db" stroke-width="1.6"/></svg></a>
</nav>

<header class="header">
  <div class="brand">
    <div class="brand-mark"></div>
    <div>
      <div class="brand-name">Betriebsgut Zukunft</div>
      <div class="brand-tag">AUTORISIERTER PROZESSBERATER</div>
    </div>
  </div>
  <div class="social"><span></span><span></span><span></span><span></span></div>
</header>

<section class="hero">
  <div class="hero-photo" role="img" aria-label="Photo of a consultant presenting to a business team in a meeting room"></div>
  <h1>BETRIEBSGUT ZUKUNFT</h1>
  <p>AUTORISIERTER PROZESSBERATER</p>
  <svg class="arrow prev" width="14" height="26" viewBox="0 0 14 26"><polyline points="12,2 2,13 12,24" fill="none" stroke="#fff" stroke-width="2"/></svg>
  <svg class="arrow next" width="14" height="26" viewBox="0 0 14 26"><polyline points="2,2 12,13 2,24" fill="none" stroke="#fff" stroke-width="2"/></svg>
</section>

<section class="welcome">
  <h2>Welcome To <em>Betriebsgut Zukunft</em></h2>
  <p>We guide small and medium sized companies through ten days of workshops and coaching. Our focus lies on leadership, further education and the health of your employees, because people are the true value of every company. Together we build teams that stay motivated, grow with new tasks and keep their strength for the long run.</p>
</section>

<section class="cards">
  <article class="card">
    <div class="card-head blue"><h3>FINIBUS BONORUM</h3><div class="card-icon"><svg width="30" height="30" viewBox="0 0 30 30"><circle cx="15" cy="15" r="11" fill="none" stroke="#1e7fb0" stroke-width="2.5"/><polyline points="9,15 13,19 21,11" fill="none" stroke="#1e7fb0" stroke-width="2.5"/></svg></div></div>
    <p>Short note on what this topic means for your team and daily work.</p>
    <div class="more"><span>Read more</span><span>›</span></div>
  </article>
  <article class="card">
    <div class="card-head orange"><h3>FINIBUS BONORUM</h3><div class="card-icon"><svg width="30" height="30" viewBox="0 0 30 30"><circle cx="15" cy="15" r="5" fill="none" stroke="#c7822e" stroke-width="2.5"/><circle cx="15" cy="15" r="11" fill="none" stroke="#c7822e" stroke-width="2.5" stroke-dasharray="4 3"/></svg></div></div>
    <p>Short note on what this topic means for your team and daily work.</p>
    <div class="more"><span>Read more</span><span>›</span></div>
  </article>
  <article class="card">
    <div class="card-head orange"><h3>FINIBUS BONORUM</h3><div class="card-icon"><svg width="30" height="30" viewBox="0 0 30 30"><rect x="6" y="8" width="18" height="14" fill="none" stroke="#c7822e" stroke-width="2.5"/><line x1="6" y1="13" x2="24" y2="13" stroke="#c7822e" stroke-width="2.5"/></svg></div></div>
    <p>Short note on what this topic means for your team and daily work.</p>
    <div class="more"><span>Read more</span><span>›</span></div>
  </article>
  <article class="card">
    <div class="card-head blue"><h3>FINIBUS BONORUM</h3><div class="card-icon"><svg width="30" height="30" viewBox="0 0 30 30"><line x1="7" y1="7" x2="23" y2="23" stroke="#1e7fb0" stroke-width="2.5"/><line x1="23" y1="7" x2="7" y2="23" stroke="#1e7fb0" stroke-width="2.5"/><circle cx="15" cy="15" r="4" fill="#1e7fb0"/></svg></div></div>
    <p>Short note on what this topic means for your team and daily work.</p>
    <div class="more"><span>Read more</span><span>›</span></div>
  </article>
</section>

<section class="services">
  <h2>Our Services</h2>
  <p class="sub">Tailored support for small and medium companies</p>
  <div class="service-row">
    <div class="service">
      <div class="service-photo" role="img" aria-label="Photo of a business leader with his team"></div>
      <div class="service-foot"><span>Leadership</span><span class="btn">Details</span></div>
    </div>
    <div class="service">
      <div class="service-photo" role="img" aria-label="Photo of colleagues talking at a desk"></div>
      <div class="service-foot"><span>Employees health</span><span class="btn">Details</span></div>
    </div>
    <div class="service">
      <div class="service-photo" role="img" aria-label="Photo of a training session with laptops"></div>
      <div class="service-foot"><span>Further education</span><span class="btn">Details</span></div>
    </div>
  </div>
</section>

<section class="testimonials">
  <h2>Testimonials</h2>
  <div class="rule"></div>
  <div class="quote-wrap">
    <div class="avatar" role="img" aria-label="Portrait photo of the client"></div>
    <div class="quote">
      <span class="mark open">“</span>
      <p>The workshops gave our leaders clear tools and our staff new energy. Communication improved within weeks, and the coaching on health topics was practical and easy to apply.</p>
      <p class="who">- Jonas Berg</p>
      <p class="role">Manager</p>
      <span class="mark close">”</span>
    </div>
  </div>
</section>

<footer class="footer">
  <div class="col-about">
    <h4>ABOUT US</h4>
    <ul><li>Home</li><li>About Us</li><li>Services</li><li>Blog</li><li>Testimonials</li></ul>
  </div>
  <div class="col-service">
    <h4>CUSTOMER SERVICE</h4>
    <ul><li>Contact Us</li><li>Terms/conditions</li></ul>
  </div>
  <div class="col-contact">
    <h4>CONTACT US</h4>
    <div class="form"><span>Name</span><span>Phone</span><span>Email</span><span>Message</span><span class="submit">Submit</span></div>
  </div>
  <div class="col-q">
    <h4>HAVE QUESTIONS?</h4>
    <p>+49 30 5550 1234</p>
    <p>kontakt@betriebsgut-zukunft.de</p>
    <p class="loc">Birkenhainweg 14, 10219 Berlin</p>
  </div>
</footer>
<div class="bottombar"><span>© COPYRIGHT 2015 BETRIEBSGUT-ZUKUNFT.DE</span><span>TOP</span></div>

</body>
</html>
```